Satchel & Sundial needs new business card design

I need a new business card design. I'm looking for out-of-the-box design which represents the freedom of being a location independent entrepreneur.
I offer coaching, retreats and trips.
I would like to see designs with and without the photo.
Colors I use are black (#000000), green (#25A796) and brown (#D7C38C)
Website satchelandsundial.example

Target Market(s)

location independent entrepreneurs, digital nomads, people looking to swap the 9 to 5 for a lifestyle business

Industry/Entity Type

Business

Contact Information for Business Card

Dorota Falkner
Your Lifestyle Business Coach, Retreat & Trip Leader
http://satchelandsundial.example
hello@satchelandsundial.example
Live a life you don't need a holiday from

Font styles to use
Serif
Sans Serif

Requirements
Must have
• One side should contain only the logo. I would also consider having the "Live a life you don't need a holiday from" on that side too (depending on how it looks)
• Please show both sides on the designs.

```html
<!DOCTYPE html>
<html lang="en">
<head>
<meta charset="utf-8">
<title>Dorota Falkner — Business Card</title>
<link rel="stylesheet" href="https://fonts.googleapis.com/css2?family=Caveat+Brush&family=Caveat:wght@500;600&family=Kalam:wght@400&display=swap">
<style>
  :root {
    --ink: #1c1a19;
    --green: #25a796;
    --green-deep: #1e8a7c;
    --brown: #d7c38c;
    --card: #f4f1ec;
    --backdrop: #d9d3cb;
  }
  * { margin: 0; padding: 0; box-sizing: border-box; }
  html, body {
    width: 1200px;
    height: 1010px;
    overflow: hidden;
    background: var(--backdrop);
  }
  .stage {
    width: 1200px;
    height: 1010px;
    display: flex;
    align-items: center;
    justify-content: center;
  }
  .business-card {
    width: 1000px;
    height: 580px;
    background: var(--card);
    border: 1px solid rgba(255,255,255,0.7);
    box-shadow: 0 10px 30px rgba(0,0,0,0.12);
    display: flex;
    flex-direction: column;
    align-items: center;
    text-align: center;
    padding-top: 70px;
  }
  .holder-name {
    font-family: "Caveat Brush", cursive;
    font-size: 66px;
    letter-spacing: 2px;
    color: var(--ink);
    text-transform: uppercase;
    line-height: 1;
  }
  .holder-role {
    font-family: "Caveat", cursive;
    font-weight: 600;
    font-size: 34px;
    color: var(--green);
    margin-top: 6px;
  }
  .contact {
    margin-top: 78px;
    font-family: "Kalam", cursive;
    font-size: 28px;
    color: var(--ink);
    line-height: 1.6;
  }
  .contact .domain { color: var(--green-deep); }
  .social-marks {
    display: flex;
    gap: 6px;
    justify-content: center;
    margin-top: 8px;
  }
  .social-marks span {
    width: 26px;
    height: 26px;
    border-radius: 5px;
    background: var(--brown);
  }
  .motto {
    margin-top: 72px;
    font-family: "Caveat Brush", cursive;
    font-size: 44px;
    color: var(--green-deep);
    text-transform: uppercase;
    letter-spacing: 1px;
  }
</style>
</head>
<body>
  <main class="stage">
    <section class="business-card">
      <h1 class="holder-name">Dorota Falkner</h1>
      <p class="holder-role">Your Lifestyle Business Coach, Retreat and Trip Leader</p>
      <div class="contact">
        <p class="email">hello@satchelandsundial.example</p>
        <p class="website">www.<span class="domain">satchelandsundial.example</span></p>
      </div>
      <div class="social-marks" aria-label="Social media links">
        <span></span><span></span><span></span>
      </div>
      <p class="motto">Live a life you don’t need a holiday from</p>
    </section>
  </main>
</body>
</html>
```